Banner ads for LP that work with same theme as below banners

Love the banner ads below. Need more with attached photos. But use the same wording, font as in below banner ads. Should be LP size 1200/627 so I can use for Pixorly and LP. Looking for great ads to use as LP ads. We do lots of ads so it will be worth your time to enter this contest you will be rewarded with a ton of work. Need several banner ads that work together. So maybe 1 of the dresses, 1 of the sweater, 1 of the leggings, 1 of the jacket

Target Market(s)

Women 24-45

Industry/Entity Type

Fashion

Requirements
Must have
• Banner ads that work for LP and Pixorly
Nice to have
• Several options to choose from
Should not have
• not sure

```html
<!DOCTYPE html>
<html lang="en">
<head>
<meta charset="utf-8">
<title>Winter Wear Collection</title>
<link rel="stylesheet" href="https://fonts.googleapis.com/css2?family=Kaushan+Script&family=Tinos:wght@400;700&display=swap">
<style>
  :root {
    --mist-light: #f1f1f2;
    --mist-mid: #d4d5d8;
    --mist-dark: #a9abaf;
    --ink: #3d3e40;
    --white: #ffffff;
    --panel-light: #e4e5e7;
    --panel-dark: #8f9196;
    --jacket: #1f3656;
    --hair: #a7743f;
  }
  * { margin: 0; padding: 0; box-sizing: border-box; }
  html, body { width: 1200px; height: 627px; overflow: hidden; }
  body { background: var(--mist-mid); }
  .banner {
    position: relative;
    width: 1200px;
    height: 627px;
    overflow: hidden;
    background:
      radial-gradient(ellipse 420px 260px at 760px 380px, var(--mist-light), transparent 70%),
      radial-gradient(ellipse 520px 320px at 1050px 80px, #bfc0c4, transparent 70%),
      linear-gradient(180deg, #cfd0d3 0%, #dcdde0 45%, #c5c6ca 100%);
  }
  .model-photo {
    position: absolute;
    left: 40px;
    top: 0;
    width: 450px;
    height: 627px;
    border-radius: 180px 180px 0 0;
    background:
      linear-gradient(180deg, #c9b4a2 0%, var(--hair) 22%, #3a4e6c 42%, var(--jacket) 70%, #9c9fa4 84%, #1a1a1c 100%);
    opacity: 0.9;
  }
  .headline {
    position: absolute;
    left: 520px;
    top: 72px;
    width: 675px;
    text-align: center;
    font-family: "Kaushan Script", cursive;
    font-size: 50px;
    color: var(--white);
    letter-spacing: 2px;
    text-shadow: 0 0 6px rgba(0,0,0,0.15);
  }
  .collection-box {
    position: absolute;
    left: 520px;
    top: 146px;
    width: 675px;
    height: 89px;
    border: 2px solid var(--white);
    box-shadow: 0 0 14px 4px rgba(255,255,255,0.9);
    background: linear-gradient(180deg, var(--panel-light), #cfd0d3);
  }
  .collection-box svg { position: absolute; inset: 0; }
  .collection-title {
    position: absolute;
    inset: 0;
    display: flex;
    align-items: center;
    justify-content: center;
    font-family: "Tinos", serif;
    font-size: 60px;
    letter-spacing: 17px;
    padding-left: 17px;
    color: var(--ink);
  }
  .shop-button {
    position: absolute;
    left: 797px;
    top: 473px;
    width: 318px;
    height: 79px;
    border: 2px solid var(--white);
    box-shadow: 0 0 10px 2px rgba(255,255,255,0.9);
    background: linear-gradient(180deg, #e9eaec, #c9cacd);
    display: flex;
    align-items: center;
    justify-content: center;
    font-family: "Tinos", serif;
    font-size: 27px;
    color: var(--ink);
    text-decoration: none;
  }
  .shop-button b { font-weight: 700; }
  .shop-button span { margin: 0 7px; }
</style>
</head>
<body>
  <main class="banner">
    <div class="model-photo" role="img" aria-label="Model with long wavy hair wearing a navy quilted puffer jacket with faux fur collar and knit hem"></div>

    <h1 class="headline">Winter Wear</h1>

    <div class="collection-box">
      <svg width="671" height="85" viewBox="0 0 671 85" aria-hidden="true">
        <polygon points="0,0 48,0 0,85" fill="var(--panel-dark)" opacity="0.75"/>
        <polygon points="671,0 671,85 630,85" fill="var(--panel-dark)" opacity="0.75"/>
      </svg>
      <h2 class="collection-title">COLLECTION</h2>
    </div>

    <a class="shop-button" href="#"><b>SHOP</b><span>THE</span><b>SEASON</b></a>
  </main>
</body>
</html>
```